Irrigation Business needs their business cards modernised and revamped

I would like to keep my current logo, colours and revamp the format of the card.

I would like the card to be clean yet important.

Im not sure if you include texture but i would like the named logo to be indented into the card etc.

show me something alive and free something thats clinical to the point yet has a feel of achievement. i would like people to go nice card.

Target Market(s)

high end clients, corporate, sports field manger, the guys that make the decisions

Industry/Entity Type

Business

Contact Information for Business Card

nformation to be included

Dean Harlow (Director)
0487305526
dean@kolvat.biz
www.kestonfieldworks.com

instagram logo
google logo
facebook logo

Colors

Designer to choose colors to be used in the design.

Requirements
Nice to have
• indentations a really nice feel to the card good texture

```html
<!DOCTYPE html>
<html lang="en">
<head>
<meta charset="utf-8">
<title>Keston Fieldworks – Business Card</title>
<link rel="stylesheet" href="https://fonts.googleapis.com/css2?family=Roboto:wght@400;700&display=swap">
<style>
  :root {
    --backdrop: #e4e4e4;
    --card: #f7f7f8;
    --card-shade: #ececef;
    --navy: #2f4f94;
    --sky: #3a8fc9;
    --green: #15974a;
    --ink: #2a2a2a;
    --white: #ffffff;
    --ghost: rgba(47, 79, 148, 0.06);
  }
  * { box-sizing: border-box; margin: 0; padding: 0; }
  html, body { width: 1200px; height: 576px; overflow: hidden; }
  body {
    background: var(--backdrop);
    font-family: "Roboto", Arial, sans-serif;
    position: relative;
  }
  .card {
    position: absolute;
    top: 138px;
    height: 294px;
    border-radius: 12px;
    background: linear-gradient(160deg, var(--white), var(--card) 55%, var(--card-shade));
    box-shadow: 0 3px 6px rgba(0,0,0,0.22);
    overflow: hidden;
  }
  .card--front { left: 82px; width: 484px; }
  .card--back { left: 602px; width: 480px; }
  .card__art { position: absolute; inset: 0; width: 100%; height: 100%; }

  .brand-name {
    position: absolute;
    font-weight: 700;
    color: var(--navy);
    white-space: nowrap;
    letter-spacing: -0.3px;
  }
  .card--front .brand-name { left: 0; right: 0; text-align: center; top: 152px; font-size: 26px; }
  .card--back .brand-name { left: 30px; width: 216px; text-align: center; top: 205px; font-size: 23px; }

  .social-row {
    position: absolute;
    display: flex;
    gap: 5px;
    align-items: center;
  }
  .social-dot {
    width: 15px; height: 15px; border-radius: 50%;
    background: var(--navy);
  }
  .card--front .social-row { left: 0; right: 0; justify-content: center; top: 264px; }

  .holder {
    position: absolute;
    right: 22px;
    top: 34px;
    text-align: right;
    color: var(--white);
  }
  .holder__name { font-size: 21px; font-weight: 700; letter-spacing: 0.3px; }
  .holder__role { font-size: 11px; margin-top: 4px; }

  .contact {
    position: absolute;
    right: 22px;
    top: 186px;
    text-align: right;
    color: var(--ink);
    font-size: 12.5px;
    line-height: 16.5px;
  }
  .contact__follow { display: flex; justify-content: flex-end; align-items: center; gap: 3px; margin-bottom: 3px; }
  .contact__follow .social-row { position: static; gap: 3px; }
  .contact__line { display: flex; justify-content: flex-end; align-items: center; gap: 7px; }
  .contact__icon { width: 10px; height: 10px; fill: var(--navy); flex: none; }
</style>
</head>
<body>

<section class="card card--front">
  <svg class="card__art" viewBox="0 0 484 294" aria-hidden="true">
    <circle cx="390" cy="138" r="104" fill="none" stroke="var(--ghost)" stroke-width="12"/>
    <circle cx="243" cy="92" r="46" fill="var(--sky)" stroke="var(--navy)" stroke-width="3"/>
    <line x1="80" y1="271" x2="198" y2="271" stroke="var(--navy)" stroke-width="2"/>
    <line x1="286" y1="271" x2="404" y2="271" stroke="var(--navy)" stroke-width="2"/>
  </svg>
  <div class="brand-name">KESTON FIELDWORKS</div>
  <div class="social-row">
    <span class="social-dot"></span><span class="social-dot"></span><span class="social-dot"></span>
  </div>
</section>

<section class="card card--back">
  <svg class="card__art" viewBox="0 0 480 294" aria-hidden="true">
    <circle cx="414" cy="182" r="100" fill="none" stroke="var(--ghost)" stroke-width="12"/>
    <path d="M0,0 H480 V122 C400,126 320,80 230,52 C150,28 70,18 0,34 Z" fill="var(--navy)"/>
    <path d="M0,46 C80,22 180,18 270,46 C180,28 90,34 0,60 Z" fill="var(--green)"/>
    <path d="M42,50 C150,34 250,56 330,96 C390,126 440,138 480,140 V146 C430,146 380,134 320,104 C240,66 150,48 42,50 Z" fill="var(--sky)"/>
    <circle cx="138" cy="138" r="58" fill="var(--sky)" stroke="var(--navy)" stroke-width="3"/>
  </svg>

  <div class="holder">
    <div class="holder__name">DEAN HARLOW</div>
    <div class="holder__role">Director</div>
  </div>

  <div class="brand-name">KESTON FIELDWORKS</div>

  <div class="contact">
    <div class="contact__follow">
      <span>Follow us on:</span>
      <div class="social-row">
        <span class="social-dot"></span><span class="social-dot"></span><span class="social-dot"></span>
      </div>
    </div>
    <div class="contact__line">
      <span>0487305526</span>
      <svg class="contact__icon" viewBox="0 0 10 10"><path d="M1 3 C1 1.5 2 1 5 1 C8 1 9 1.5 9 3 L7 3.6 L6.5 2.6 H3.5 L3 3.6 Z M2.5 5 H7.5 L8.5 9 H1.5 Z"/></svg>
    </div>
    <div class="contact__line">
      <span>dean@kolvat.biz</span>
      <svg class="contact__icon" viewBox="0 0 10 10"><path d="M0 2 H10 V8.5 H0 Z M0.8 2.6 L5 5.8 L9.2 2.6" stroke="var(--white)" stroke-width="0.8"/></svg>
    </div>
    <div class="contact__line">
      <span>www.kestonfieldworks.com</span>
      <svg class="contact__icon" viewBox="0 0 10 10"><circle cx="5" cy="5" r="4.5"/><path d="M0.5 5 H9.5 M5 0.5 V9.5 M2 2.5 Q5 4 8 2.5 M2 7.5 Q5 6 8 7.5" stroke="var(--white)" stroke-width="0.6" fill="none"/></svg>
    </div>
  </div>
</section>

</body>
</html>
```